Homepage for Travel NFT Marketplace

Hi there!
We are building a Travel Marketplace that incorporates NFTs. We are looking for a full page redesign of the homepage for this marketplace.
You can find the instructions along with all the content here at https://www.sharevault.net/sh/7qw3mzx8kpl2vr4/BBHtxLmQpwZeKnaRsTuVwXyhd?dl=0
We look forward to seeing your submissions!
Industry/Entity Type
Tourism
Number of Pages Required
1 page
Font styles to use
Sans Serif
Colors
0094D4
00A9DD
6FCCEA
C7EBF8
E9F6FB
00AB8E
00BBA5
67D7C9
C6EFE9
E9F9F6
F0912C
F2A743
F7CA91
FBE8D2
FDF5EE
A7469A
B969AE
D3A5CF
EDDBEB
F8F0F9
6B429C
8869AF
B7A5CE
E3DAEB
F3F0F8
Requirements
Must have
- Clean, Modern & Fun!
Should not have
- Messy or Overcrowded

```html
<!DOCTYPE html>
<html lang="en">
<head>
<meta charset="utf-8">
<title>Nomad Ledger — Travel NFT Marketplace</title>
<link href="https://fonts.googleapis.com/css2?family=Mulish:wght@400;600;700;800;900&family=Montserrat:wght@900&display=swap" rel="stylesheet">
<style>
:root{
  --magenta:#d4169f;
  --purple:#7a3fc6;
  --blue:#2fa6f2;
  --cyan:#28c3f2;
  --ink:#1f1b2e;
  --grey-text:#2c2c34;
  --soft-bg:#f6f6f8;
  --white:#ffffff;
}
*{box-sizing:border-box;margin:0;padding:0}
html,body{width:1200px;height:4732px;overflow:hidden}
body{position:relative;background:var(--white);font-family:"Mulish",sans-serif;color:var(--ink)}
.abs{position:absolute}

/* nav */
.site-nav{position:absolute;left:0;top:0;width:1200px;height:81px;background:var(--white);box-shadow:0 2px 6px rgba(0,0,0,.06);z-index:5}
.brand{position:absolute;left:112px;top:22px;display:flex;align-items:center;gap:12px;font-size:20px;font-weight:600;color:var(--ink)}
.brand-dot{width:34px;height:34px;border-radius:50%;background:var(--purple)}
.nav-links{position:absolute;left:0;top:0;height:81px}
.nav-link{position:absolute;top:30px;font-size:15px;font-weight:600;color:var(--ink);white-space:nowrap}
.nav-link.active{top:0;height:81px;width:103px;left:426px;background:#f1e8f8;color:var(--magenta);text-align:center;line-height:81px;border-bottom:3px solid var(--purple)}
.nav-icon{position:absolute;top:16px;width:50px;height:50px;border-radius:50%;background:#eeeef2;display:flex;align-items:center;justify-content:center}

/* hero */
.hero{position:absolute;left:0;top:81px;width:1200px;height:661px;background:var(--soft-bg);overflow:hidden}
.glow{position:absolute;border-radius:50%;filter:blur(40px)}
.hero-title{position:absolute;left:0;width:1200px;text-align:center;font-size:44px;font-weight:800;line-height:56px;color:var(--ink)}
.t-grad{background:linear-gradient(90deg,var(--magenta),var(--purple));-webkit-background-clip:text;background-clip:text;color:transparent}
.t-outline{color:transparent;-webkit-text-stroke:1.5px var(--magenta);font-weight:700}
.hero-crowd{position:absolute;left:320px;top:165px;width:560px;height:410px;border-radius:40px;background:linear-gradient(160deg,#c9b79a,#6f7f8f 60%,#3b4a5c)}
.hero-word{position:absolute;left:0;top:430px;width:1200px;text-align:center;font-family:"Montserrat",sans-serif;font-weight:900;font-size:176px;letter-spacing:2px;line-height:180px;background:linear-gradient(90deg,var(--cyan) 10%,var(--purple) 50%,var(--magenta) 90%);-webkit-background-clip:text;background-clip:text;color:transparent;opacity:.92}
.balloon-art{position:absolute;border-radius:16px;background:linear-gradient(180deg,#f2a743,#e0709a)}

/* hub */
.hub{position:absolute;left:0;top:742px;width:1200px;height:829px;background:var(--white)}
.hub-tile{position:absolute;width:156px;height:143px;border:3px solid var(--magenta);box-shadow:4px 4px 0 var(--cyan)}
.hub-photo{position:absolute;width:145px;height:145px}
.hub-center{position:absolute;left:456px;top:329px;width:184px;height:184px;border-radius:50%;background:var(--white);box-shadow:0 8px 30px rgba(120,60,180,.18);display:flex;align-items:center;justify-content:center;text-align:center;font-size:22px;font-weight:800;color:var(--purple);line-height:26px}

/* stats */
.stats{position:absolute;left:0;top:1571px;width:1200px;height:282px;background:linear-gradient(90deg,#d413c9 0%,#9d2ee0 40%,#6a5cf0 70%,#2fb0ff 100%);overflow:hidden}
.stat{position:absolute;top:110px;display:flex;gap:14px;color:var(--white)}
.stat-value{font-size:20px;font-weight:800;line-height:26px}
.stat-label{font-size:13px;font-weight:700;line-height:20px}

/* section titles */
.section-title{position:absolute;left:0;width:1200px;text-align:center;font-size:37px;font-weight:800;color:var(--ink)}
.section-title .accent{color:var(--magenta)}

/* locations */
.location{position:absolute;width:210px;height:212px;overflow:hidden;box-shadow:0 2px 6px rgba(0,0,0,.12)}
.location-img{position:absolute;inset:0}
.location-label{position:absolute;left:0;bottom:0;width:100%;height:44px;background:rgba(255,255,255,.72);text-align:center;line-height:44px;font-size:19px;font-weight:800;color:var(--ink)}
.g-cove{background:linear-gradient(180deg,#a9b8c6 0%,#6b7a5a 35%,#3fb6b0 62%,#e9e2d2 80%)}
.g-sunset{background:linear-gradient(180deg,#5a6b84 0%,#f2c06a 38%,#f49b3a 50%,#6d6e78 70%,#3d3f47 100%)}
.g-palms{background:linear-gradient(180deg,#8cc0e8 0%,#cfe5f4 45%,#3c6a3d 60%,#e8dcc3 85%)}
.g-peak{background:linear-gradient(180deg,#4d8fd8 0%,#b6d4f0 30%,#355e2c 55%,#6b8f3a 80%,#9cc0d9 100%)}

/* apart */
.apart{position:absolute;left:0;top:2527px;width:1200px;height:1167px;background:var(--soft-bg);overflow:hidden}
.road-art{position:absolute;left:455px;top:290px;width:225px;height:877px;border-radius:110px 110px 0 0;background:linear-gradient(180deg,#3a3a42,#141418)}
.step{position:absolute;width:250px}
.step.right{text-align:right}
.step-title{font-size:20px;font-weight:600;line-height:24px;margin-bottom:4px}
.step-title.blue{color:var(--blue)}
.step-title.pink{color:var(--magenta)}
.step-text{font-size:11.5px;font-weight:800;line-height:19px;color:var(--grey-text)}
.art{position:absolute;border-radius:24px}

/* nfts */
.nft{position:absolute;width:213px;height:263px}
.nft.pink{background:radial-gradient(circle at 50% 55%,#ffffff 30%,#f3c3e6 75%,#e889cf 100%)}
.nft.blue{background:radial-gradient(circle at 50% 55%,#ffffff 30%,#c6e7fa 75%,#8fd0f5 100%)}
.nft-figure{position:absolute;left:38px;top:50px;width:140px;height:213px;border-radius:20px 20px 0 0}
.btn{position:absolute;left:491px;top:4469px;width:220px;height:66px;border-radius:33px;background:linear-gradient(90deg,var(--cyan),var(--purple) 60%,var(--magenta));color:var(--white);font-size:19px;font-weight:700;text-align:center;line-height:66px;box-shadow:0 6px 16px rgba(160,50,200,.3)}

/* footer */
.site-footer{position:absolute;left:0;top:4622px;width:1200px;height:110px;background:linear-gradient(90deg,#2f8cf0,#8a3fd0 60%,#d419b8);color:var(--white);font-size:14px;font-weight:600}
.copyright{position:absolute;left:112px;top:42px}
.legal{position:absolute;right:112px;top:42px}
</style>
</head>
<body>

<header class="site-nav">
  <div class="brand"><span class="brand-dot"></span>Nomad Ledger</div>
  <nav class="nav-links">
    <span class="nav-link active">Home</span>
    <span class="nav-link" style="left:553px">About</span>
    <span class="nav-link" style="left:636px">NFT</span>
    <span class="nav-link" style="left:702px">Trips</span>
    <span class="nav-link" style="left:776px">Auctions</span>
    <span class="nav-link" style="left:874px">The Pot</span>
  </nav>
  <span class="nav-icon" style="left:962px">
    <svg width="24" height="24" viewBox="0 0 24 24"><circle cx="12" cy="12" r="10" fill="none" stroke="#7a3fc6" stroke-width="2"/><circle cx="12" cy="10" r="3.5" fill="#d4169f"/><path d="M5.5 18c2-3 11-3 13 0" stroke="#d4169f" stroke-width="2" fill="none"/></svg>
  </span>
  <span class="nav-icon" style="left:1038px">
    <svg width="24" height="24" viewBox="0 0 24 24"><rect x="3" y="6" width="18" height="14" rx="3" fill="#7a3fc6"/><rect x="14" y="11" width="7" height="5" rx="1.5" fill="#d4169f"/></svg>
  </span>
</header>

<section class="hero">
  <div class="glow" style="left:-60px;top:120px;width:260px;height:260px;background:rgba(212,22,159,.22)"></div>
  <div class="glow" style="left:1000px;top:140px;width:260px;height:240px;background:rgba(122,63,198,.2)"></div>
  <div class="balloon-art" style="left:20px;top:60px;width:112px;height:130px" role="img" aria-label="Hot air balloon illustration"></div>
  <div class="balloon-art" style="left:940px;top:42px;width:58px;height:70px" role="img" aria-label="Small hot air balloon illustration"></div>
  <div class="balloon-art" style="left:1128px;top:470px;width:72px;height:95px" role="img" aria-label="Hot air balloon illustration"></div>
  <h1 class="hero-title" style="top:54px">Bridging The Gap <span class="t-outline">between</span><br><span class="t-grad">Crypto &amp;</span> Real World <span class="t-grad">Adventures</span></h1>
  <div class="hero-crowd" role="img" aria-label="Illustration of a group of cheerful backpackers reading a map together"></div>
  <div class="hero-word">NOMADS</div>
</section>

<section class="hub">
  <svg class="abs" style="left:0;top:0" width="1200" height="829" viewBox="0 0 1200 829">
    <g fill="none" stroke="#333" stroke-width="1.8" stroke-dasharray="5 5">
      <path d="M530 330 V180 Q530 170 520 170 H455"/>
      <path d="M530 510 V635 Q530 645 520 645 H455"/>
      <path d="M456 421 H358"/>
      <path d="M584 330 V180 Q584 168 596 168 H670"/>
      <path d="M584 510 V635 Q584 645 596 645 H670"/>
      <path d="M640 421 H670"/>
    </g>
    <g fill="#333">
      <path d="M447 170 l10 -5 v10z"/>
      <path d="M447 645 l10 -5 v10z"/>
      <path d="M350 421 l10 -5 v10z"/>
      <path d="M676 168 l-10 -5 v10z"/>
      <path d="M676 645 l-10 -5 v10z"/>
      <path d="M676 421 l-10 -5 v10z"/>
    </g>
  </svg>
  <div class="hub-tile" style="left:283px;top:109px;background:linear-gradient(160deg,#c8e3d6,#6b8f5c 50%,#3e4a5a)" role="img" aria-label="Illustration of a bearded traveller with a banjo"></div>
  <div class="hub-tile" style="left:158px;top:351px;background:linear-gradient(160deg,#9fd6cf,#3ea0b8 45%,#e0559a 75%,#f0c84a)" role="img" aria-label="Illustration of a painted camper van"></div>
  <div class="hub-tile" style="left:283px;top:594px;background:linear-gradient(160deg,#cdeef0,#7fc4c0 50%,#4a5b7a)" role="img" aria-label="Illustration of a group of hikers"></div>
  <div class="hub-center">Nomad<br>Ledger</div>
  <div class="hub-photo" style="left:680px;top:111px;background:linear-gradient(180deg,#6ea8e0,#3d6f9b 45%,#7a6a4c 75%,#4e4f38)" role="img" aria-label="Photo of a cyclist by a mountain lake"></div>
  <div class="hub-photo" style="left:886px;top:111px;background:linear-gradient(180deg,#a8c8e6,#8fa3a0 35%,#5f8a48 65%,#3f5e2e)" role="img" aria-label="Photo of mountain bikers on an alpine trail"></div>
  <div class="hub-photo" style="left:680px;top:351px;background:linear-gradient(180deg,#9cc6ec,#c9b484 40%,#7a8a5a 70%,#a59a84)" role="img" aria-label="Photo of tourists at an ancient aqueduct"></div>
  <div class="hub-photo" style="left:886px;top:351px;background:linear-gradient(180deg,#7fb4e8,#c6d8e8 30%,#c96a4a 60%,#7a4030)" role="img" aria-label="Photo of a traveller overlooking red rooftops"></div>
  <div class="hub-photo" style="left:680px;top:587px;background:linear-gradient(180deg,#e9dcd0,#c9a58a 40%,#f2efe8 70%,#a8865e)" role="img" aria-label="Photo of an older couple walking on a beach"></div>
  <div class="hub-photo" style="left:886px;top:587px;background:linear-gradient(180deg,#8ec6ee,#3bb5c9 45%,#2a8fa8 70%,#e8e0d0)" role="img" aria-label="Photo of a traveller in a colourful hat by a turquoise bay"></div>
</section>

<section class="stats">
  <div class="balloon-art" style="left:56px;top:-30px;width:112px;height:110px" role="img" aria-label="Hot air balloon illustration"></div>
  <div class="stat" style="left:110px">
    <svg width="54" height="48" viewBox="0 0 54 48"><path d="M3 12l14-5 18 6 16-6v33l-16 6-18-6-14 5z" fill="none" stroke="#fff" stroke-width="3"/><circle cx="36" cy="10" r="6" fill="#fff"/></svg>
    <div><div class="stat-value">$ 45,6780</div><div class="stat-label">Our adventures are available</div></div>
  </div>
  <div class="stat" style="left:500px">
    <svg width="54" height="48" viewBox="0 0 54 48"><rect x="4" y="14" width="46" height="10" fill="#fff"/><rect x="8" y="26" width="38" height="20" fill="none" stroke="#fff" stroke-width="3"/><rect x="24" y="14" width="6" height="32" fill="#fff"/></svg>
    <div><div class="stat-value">$ 1,45,67890</div><div class="stat-label">Gives its Prizes to our</div></div>
  </div>
  <div class="stat" style="left:875px">
    <svg width="54" height="48" viewBox="0 0 54 48"><rect x="3" y="10" width="44" height="34" rx="6" fill="#fff"/><rect x="32" y="20" width="18" height="14" rx="4" fill="#9d2ee0" stroke="#fff" stroke-width="3"/></svg>
    <div><div class="stat-value">$ 145,670</div><div class="stat-label">Wallet Lorem Ipsum</div></div>
  </div>
</section>

<h2 class="section-title" style="top:1914px">Our <span class="accent">Locations</span></h2>
<div class="location" style="left:112px;top:1996px"><div class="location-img g-cove" role="img" aria-label="Photo of a beach cove below steep mountains"></div><span class="location-label">Ullamco Laboris</span></div>
<div class="location" style="left:368px;top:1996px"><div class="location-img g-sunset" role="img" aria-label="Photo of a sunset over a rocky shore"></div><span class="location-label">Tempor Incididu</span></div>
<div class="location" style="left:623px;top:1996px"><div class="location-img g-palms" role="img" aria-label="Photo of palm trees on a sandy beach"></div><span class="location-label">Sunt Explicabo</span></div>
<div class="location" style="left:878px;top:1996px"><div class="location-img g-peak" role="img" aria-label="Photo of a green volcanic peak"></div><span class="location-label">Acsantium Dolor</span></div>
<div class="location" style="left:112px;top:2236px"><div class="location-img g-cove" role="img" aria-label="Photo of a beach cove below steep mountains"></div><span class="location-label">Ullamco Laboris</span></div>
<div class="location" style="left:368px;top:2236px"><div class="location-img g-sunset" role="img" aria-label="Photo of a sunset over a rocky shore"></div><span class="location-label">Tempor Incididu</span></div>
<div class="location" style="left:623px;top:2236px"><div class="location-img g-palms" role="img" aria-label="Photo of palm trees on a sandy beach"></div><span class="location-label">Sunt Explicabo</span></div>
<div class="location" style="left:878px;top:2236px"><div class="location-img g-peak" role="img" aria-label="Photo of a green volcanic peak"></div><span class="location-label">Acsantium Dolor</span></div>

<section class="apart">
  <div class="glow" style="left:-80px;top:140px;width:260px;height:260px;background:rgba(212,22,159,.15)"></div>
  <div class="glow" style="left:1000px;top:500px;width:260px;height:260px;background:rgba(40,195,242,.13)"></div>
  <h2 class="section-title" style="top:70px">What Sets Us <span class="accent">Apart?</span></h2>

  <div class="road-art" role="img" aria-label="Illustration of a winding road leading up to the horizon"></div>

  <div class="art" style="left:240px;top:160px;width:210px;height:125px;background:linear-gradient(160deg,#d8ecef,#7fb6b8 50%,#5a6b8a)" role="img" aria-label="Illustration of hikers and a banjo player"></div>
  <div class="art" style="left:920px;top:240px;width:170px;height:120px;background:linear-gradient(180deg,#f6f6f8,#4f9b3a 50%,#8bbd4a)" role="img" aria-label="Illustration of pine trees on a grassy hill"></div>
  <div class="art" style="left:700px;top:385px;width:170px;height:130px;background:linear-gradient(160deg,#9fd6cf,#3ea0b8 45%,#e0559a 75%,#f0c84a)" role="img" aria-label="Illustration of a painted camper van"></div>
  <div class="art" style="left:112px;top:560px;width:165px;height:100px;background:linear-gradient(180deg,#6bb54a,#2f7a2c)" role="img" aria-label="Illustration of a row of small pine trees"></div>
  <div class="art" style="left:300px;top:520px;width:130px;height:145px;background:linear-gradient(160deg,#c8e3d6,#6b8f5c 50%,#3e4a5a)" role="img" aria-label="Illustration of a bearded traveller with a banjo"></div>
  <div class="art" style="left:790px;top:690px;width:190px;height:125px;background:linear-gradient(160deg,#e6eef0,#6f8fb0 40%,#a45a9a 70%,#5a3a7a)" role="img" aria-label="Illustration of a speaker presenting to a group"></div>
  <div class="art" style="left:298px;top:810px;width:150px;height:160px;background:linear-gradient(180deg,#f3c23a,#9b3fd0 45%,#8a6440 75%,#5a3e28)" role="img" aria-label="Illustration of a trophy coin on a wooden stand"></div>
  <div class="art" style="left:0;top:990px;width:160px;height:177px;border-radius:0 40px 0 0;background:linear-gradient(180deg,#8bc34a,#3f8a2e)" role="img" aria-label="Illustration of leafy trees"></div>
  <div class="art" style="left:775px;top:1035px;width:130px;height:110px;background:linear-gradient(180deg,#d9a43a,#7a5a2a)" role="img" aria-label="Illustration of a pot of gold coins"></div>
  <div class="art" style="left:920px;top:1050px;width:280px;height:117px;border-radius:60% 40% 0 0;background:linear-gradient(180deg,#5a8fd0,#3b6cb0 45%,#6aa83a 75%,#4b8a2e)" role="img" aria-label="Illustration of mountains with a flag on the summit"></div>

  <svg class="abs" style="left:0;top:0" width="1200" height="1167" viewBox="0 0 1200 1167">
    <defs>
      <linearGradient id="hexStroke" x1="0" y1="0" x2="1" y2="1"><stop offset="0" stop-color="#d4169f"/><stop offset=".5" stop-color="#7a3fc6"/><stop offset="1" stop-color="#28c3f2"/></linearGradient>
      <linearGradient id="numFill" x1="0" y1="0" x2="1" y2="0"><stop offset="0" stop-color="#d4169f"/><stop offset="1" stop-color="#2fa6f2"/></linearGradient>
    </defs>
    <g fill="#fff" stroke="url(#hexStroke)" stroke-width="7">
      <polygon points="628,196 665,217 665,261 628,282 591,261 591,217"/>
      <polygon points="430,376 467,397 467,441 430,462 393,441 393,397"/>
      <polygon points="770,539 807,560 807,604 770,625 733,604 733,560"/>
      <polygon points="566,703 603,724 603,768 566,789 529,768 529,724"/>
      <polygon points="693,889 730,910 730,954 693,975 656,954 656,910"/>
      <polygon points="456,1072 493,1093 493,1137 456,1158 419,1137 419,1093"/>
    </g>
    <g font-family="Mulish, sans-serif" font-weight="700" font-size="36" fill="url(#numFill)" text-anchor="middle">
      <text x="628" y="252">01</text>
      <text x="430" y="432">02</text>
      <text x="770" y="595">03</text>
      <text x="566" y="759">04</text>
      <text x="693" y="945">05</text>
      <text x="456" y="1128">06</text>
    </g>
  </svg>

  <div class="step" style="left:687px;top:204px"><div class="step-title blue">The Adventures</div><p class="step-text">We dig deep in our research &amp; work with local guides to create unique experiences not found anywhere else.</p></div>
  <div class="step right" style="left:112px;top:384px"><div class="step-title pink">Intentional Travel</div><p class="step-text">We give you the ability to have a meaningful impact on local communities and offset the emissions from your travels.</p></div>
  <div class="step" style="left:829px;top:548px"><div class="step-title blue">Keep it Simple</div><p class="step-text">No planning, no stress... Just arrive at your destination and our guides will take it from there!</p></div>
  <div class="step right" style="left:200px;top:712px"><div class="step-title pink">Fellow Nomads</div><p class="step-text">For group trips, you will meet like-minded folk within the Nomad Ledger community on your adventures.</p></div>
  <div class="step" style="left:752px;top:897px"><div class="step-title blue">Customer Experience</div><p class="step-text">After booking a trip, all correspondence is done through Chatterbox, which is quick, easy and efficient.</p></div>
  <div class="step right" style="left:138px;top:1081px"><div class="step-title pink">Pure Crypto Baby</div><p class="step-text">The world's first travel agency to exclusively accept cryptocurrencies. That's right, we're a crypto only zone.</p></div>
</section>

<h2 class="section-title" style="top:3755px">Nomad Ledger <span class="accent">NFTs</span></h2>
<div class="nft pink" style="left:112px;top:3835px" role="img" aria-label="NFT character artwork in a pink hat"><div class="nft-figure" style="background:linear-gradient(180deg,#b8389a,#8a5a3a 40%,#e88aa0)"></div></div>
<div class="nft blue" style="left:368px;top:3835px" role="img" aria-label="NFT character artwork with a teal cap"><div class="nft-figure" style="background:linear-gradient(180deg,#3ab8a0,#f08a2a 40%,#6a3fb0)"></div></div>
<div class="nft pink" style="left:621px;top:3835px" role="img" aria-label="NFT character artwork with sunglasses"><div class="nft-figure" style="background:linear-gradient(180deg,#5a4a3e,#8a7560 50%,#3a302a)"></div></div>
<div class="nft blue" style="left:875px;top:3835px" role="img" aria-label="NFT character artwork in a green beanie"><div class="nft-figure" style="background:linear-gradient(180deg,#2f6a4a,#b8a23a 45%,#f2f2f2)"></div></div>
<div class="nft pink" style="left:112px;top:4126px" role="img" aria-label="NFT character artwork in a pink hat"><div class="nft-figure" style="background:linear-gradient(180deg,#b8389a,#8a5a3a 40%,#e88aa0)"></div></div>
<div class="nft blue" style="left:368px;top:4126px" role="img" aria-label="NFT character artwork with a teal cap"><div class="nft-figure" style="background:linear-gradient(180deg,#3ab8a0,#f08a2a 40%,#6a3fb0)"></div></div>
<div class="nft pink" style="left:621px;top:4126px" role="img" aria-label="NFT character artwork with sunglasses"><div class="nft-figure" style="background:linear-gradient(180deg,#5a4a3e,#8a7560 50%,#3a302a)"></div></div>
<div class="nft blue" style="left:875px;top:4126px" role="img" aria-label="NFT character artwork in a green beanie"><div class="nft-figure" style="background:linear-gradient(180deg,#2f6a4a,#b8a23a 45%,#f2f2f2)"></div></div>
<a class="btn">Explore Our NFTs</a>

<footer class="site-footer">
  <span class="copyright">Copyrights@2022.Nomadledger.All Rights Reserved</span>
  <span class="legal">Privacy Policy &nbsp;| &nbsp;Terms &amp; Conditions</span>
</footer>

</body>
</html>
```